Luxury Business Card Design for High-End Window Treatments

Gilded Slatworks
Custom Plantation Shutters & Architectural Shading Systems

⸻

BACK

Daniel Trevick
Owner

Custom Interior & Exterior Window Treatments

919-555-0148
gildedslatworks.com

I have included a picture that I’m hoping we can use on the back, but I’m also wondering if you can get rid of the ladder? Should we get rid of shutters , shades and blinds underneath Gilded Slatworks?

Target Market(s)

High-end residential homeowners, custom home builders, architects, interior designers, and luxury renovation clients seeking premium plantation shutters and motorized architectural shading systems.

Industry/Entity Type

Custom Window treatments

Contact Information for Business Card

Front Gilded Slatworks Custom Plantation Shutters Motorized Architectural Shading Systems BACK Daniel Trevick Owner 919-555-0148 GildedSlatworks.com Custom Interior & Exterior Window Treatments By Appointment

Requirements
Nice to have
• Not 100% sure on nice to halves or the color but you can definitely check out my website to get a better understanding of what I’m trying to do

```html
<!DOCTYPE html>
<html lang="en">
<head>
<meta charset="utf-8">
<title>Gilded Slatworks – Business Card</title>
<link href="https://fonts.googleapis.com/css2?family=Fauna+One&family=Lora:wght@400;500&display=swap" rel="stylesheet">
<style>
  :root {
    --stage: #5a5a5c;
    --card-black: #0f0f10;
    --cream: #ece6d8;
    --gold: #f4d35e;
    --band-yellow: #fde36e;
    --ink: #141414;
    --photo-sky: #6f8aa3;
    --photo-mid: #3a4048;
    --photo-low: #2b3326;
  }
  * { box-sizing: border-box; margin: 0; padding: 0; }
  html, body { width: 900px; height: 1200px; overflow: hidden; }
  body { background: var(--stage); position: relative; }

  .card {
    position: absolute;
    left: 135px;
    width: 630px;
    height: 357px;
    background: var(--card-black);
    overflow: hidden;
  }
  .card--front { top: 214px; }
  .card--back { top: 628px; }

  /* Front */
  .front-photo {
    position: absolute;
    right: 0; top: 0;
    width: 420px; height: 100%;
    background:
      linear-gradient(90deg, var(--card-black) 0%, rgba(15,15,16,0.6) 30%, rgba(15,15,16,0) 60%),
      linear-gradient(180deg, var(--photo-sky) 0%, var(--photo-mid) 35%, #4a4f56 60%, var(--photo-low) 100%);
  }
  .front-brand {
    position: absolute;
    left: 40px; top: 88px;
    width: 305px;
    text-align: center;
  }
  .wordmark {
    font-family: "Fauna One", serif;
    color: var(--cream);
    line-height: 1;
  }
  .front-brand .wordmark { font-size: 56px; }
  .wordmark span { display: block; }
  .wordmark span + span { margin-top: 8px; }
  .services {
    font-family: "Fauna One", serif;
    color: var(--gold);
    word-spacing: 0.5em;
  }
  .front-brand .services { font-size: 23px; margin-top: 22px; }
  .front-url {
    font-family: "Lora", serif;
    color: #fff;
    font-size: 18px;
    letter-spacing: 0.04em;
    margin-top: 14px;
  }

  /* Back */
  .back-brand {
    position: absolute;
    left: 0; right: 0; top: 48px;
    text-align: center;
  }
  .back-brand .wordmark { font-size: 44px; }
  .back-brand .wordmark span + span { margin-top: 6px; }
  .back-brand .services { font-size: 17px; margin-top: 14px; }

  .contact-row {
    position: absolute;
    top: 211px; left: 0; right: 0;
    height: 58px;
  }
  .person {
    position: absolute;
    right: 332px; top: 0;
    text-align: right;
    font-family: "Fauna One", serif;
  }
  .person-name { color: var(--gold); font-size: 27px; line-height: 1.1; }
  .person-role { color: var(--cream); font-size: 18px; letter-spacing: 0.06em; font-family: "Lora", serif; }
  .divider {
    position: absolute;
    left: 315px; top: 0;
    width: 1.5px; height: 57px;
    background: var(--cream);
  }
  .phone {
    position: absolute;
    left: 331px; top: 16px;
    display: flex; align-items: center; gap: 10px;
    font-family: "Lora", serif;
    color: #fff;
    font-size: 24px;
    letter-spacing: 0.08em;
  }
  .phone svg { width: 15px; height: 15px; fill: var(--gold); }

  .appointment-band {
    position: absolute;
    left: 0; right: 0; top: 305px;
    height: 29px;
    background: var(--band-yellow);
    color: var(--ink);
    font-family: "Lora", serif;
    font-weight: 500;
    font-size: 16.5px;
    text-align: center;
    line-height: 29px;
  }
</style>
</head>
<body>

<section class="card card--front">
  <div class="front-photo" role="img" aria-label="Photo of a two-storey house porch with exterior shades, columns and shrubs under a blue sky"></div>
  <div class="front-brand">
    <div class="wordmark"><span>Gilded</span><span>Slatworks</span></div>
    <div class="services">Shutters Shades Blinds</div>
    <div class="front-url">www.gildedslatworks.com</div>
  </div>
</section>

<section class="card card--back">
  <div class="back-brand">
    <div class="wordmark"><span>Gilded</span><span>Slatworks</span></div>
    <div class="services">Shutters Shades Blinds</div>
  </div>
  <div class="contact-row">
    <div class="person">
      <div class="person-name">Daniel Trevick</div>
      <div class="person-role">Owner</div>
    </div>
    <div class="divider"></div>
    <div class="phone">
      <svg viewBox="0 0 24 24" aria-hidden="true"><path d="M6.6 10.8c1.4 2.8 3.8 5.1 6.6 6.6l2.2-2.2c.3-.3.7-.4 1-.2 1.1.4 2.3.6 3.6.6.6 0 1 .4 1 1V20c0 .6-.4 1-1 1C10.6 21 3 13.4 3 4c0-.6.4-1 1-1h3.5c.6 0 1 .4 1 1 0 1.3.2 2.5.6 3.6.1.3 0 .7-.2 1l-2.3 2.2z"/></svg>
      <span>919-555-0148</span>
    </div>
  </div>
  <div class="appointment-band">Custom Interior &amp; Exterior Window Treatments By Appointment</div>
</section>

</body>
</html>
```